Business Card Design using new attached logo

We are a family run Plumbing and Heating firm looking to improve our company image with an improved business card and new logo.We are looking to keep the company colour (Blue) involved in our design

Reason: New logo added which needs to be incorporated on designs

Industry/Entity Type

Business

Contact Information for Business Card

See attachment of all info required.

Requirements
Must have
• We have just picked a new company logo which is attached.
• Could you please provide your business card designs using this logo.
• We are looking for the logo on the back as well as the front with all the info required

```html
<!DOCTYPE html>
<html lang="en">
<head>
<meta charset="utf-8">
<title>Business Card – Front and Back</title>
<link rel="stylesheet" href="https://fonts.googleapis.com/css2?family=Open+Sans:wght@600;700;800&family=Tinos&display=swap">
<style>
  :root {
    --page-bg: #e6e6e6;
    --card-white: #ffffff;
    --navy: #0d1b7c;
    --sky: #1fb1e2;
    --ink: #111111;
    --logo-text: #ffffff;
  }
  html, body {
    margin: 0;
    padding: 0;
    width: 1200px;
    height: 903px;
    overflow: hidden;
    background: var(--page-bg);
  }
  .card {
    position: absolute;
    left: 250px;
    width: 700px;
    height: 400px;
    background: var(--card-white);
    box-shadow: 0 8px 24px rgba(0,0,0,0.18);
    overflow: hidden;
  }
  .card-back { top: 34px; }
  .card-front { top: 469px; }
  .card-shapes {
    position: absolute;
    inset: 0;
    width: 700px;
    height: 400px;
  }

  /* brand lockup */
  .brand {
    position: absolute;
    display: flex;
    align-items: center;
    gap: 12px;
    color: var(--logo-text);
    font-family: "Open Sans", Arial, sans-serif;
    font-weight: 700;
  }
  .brand-dot {
    width: 17px;
    height: 17px;
    border-radius: 50%;
    background: var(--logo-text);
  }
  .brand-name { line-height: 1; }
  .brand-name .main {
    display: block;
    font-size: 40px;
    letter-spacing: 1px;
  }
  .brand-name .sub {
    display: block;
    font-size: 15px;
    letter-spacing: 7px;
    margin-top: 5px;
  }
  .card-front .brand { left: 470px; top: 90px; }
  .card-back .brand { left: 40px; top: 30px; }

  /* front: holder */
  .holder {
    position: absolute;
    left: 46px;
    top: 98px;
  }
  .holder-name {
    margin: 0;
    font-family: "Open Sans", Arial, sans-serif;
    font-weight: 800;
    font-size: 30px;
    letter-spacing: 0.4px;
    color: var(--ink);
    line-height: 1.1;
  }
  .holder-role {
    margin: 3px 0 0 56px;
    font-family: "Tinos", "Times New Roman", serif;
    font-size: 28px;
    color: var(--ink);
    line-height: 1.1;
  }

  /* back: contact block */
  .contact {
    position: absolute;
    right: 36px;
    top: 170px;
    margin: 0;
    text-align: right;
    font-family: "Open Sans", Arial, sans-serif;
    font-weight: 600;
    font-size: 17px;
    line-height: 25px;
    color: var(--logo-text);
    font-style: normal;
  }
  .contact .street { font-weight: 700; }
</style>
</head>
<body>
  <section class="card card-back" aria-label="Card back">
    <svg class="card-shapes" viewBox="0 0 700 400" aria-hidden="true">
      <defs>
        <filter id="back-shadow" x="-20%" y="-20%" width="140%" height="160%">
          <feDropShadow dx="4" dy="10" stdDeviation="7" flood-color="#000" flood-opacity="0.35"/>
        </filter>
      </defs>
      <rect class="sky-band" x="0" y="150" width="700" height="160" fill="var(--sky)"/>
      <path class="navy-tab" d="M0 0 H340 V102 Q340 130 312 130 H0 Z"
            fill="var(--navy)" filter="url(#back-shadow)"/>
    </svg>

    <div class="brand">
      <span class="brand-dot"></span>
      <span class="brand-name">
        <span class="main">KESTREL</span>
        <span class="sub">SERVICES</span>
      </span>
    </div>

    <address class="contact">
      <span class="street">14 ELM PARADE</span><br>
      HARLOW ROAD, ASHFORD, SURREY TW15 2QP<br>
      Telephone: 020 7946 0321<br>
      Mobile: 07700 900482<br>
      daniel@kestrelservices.co.uk
    </address>
  </section>

  <section class="card card-front" aria-label="Card front">
    <svg class="card-shapes" viewBox="0 0 700 400" aria-hidden="true">
      <defs>
        <filter id="tab-shadow" x="-20%" y="-20%" width="140%" height="160%">
          <feDropShadow dx="-5" dy="10" stdDeviation="7" flood-color="#000" flood-opacity="0.35"/>
        </filter>
      </defs>
      <rect class="navy-band" x="0" y="196" width="700" height="124" fill="var(--navy)"/>
      <path class="sky-tab" d="M389 35 H700 V247 H426 Q412 247 409 233 L372 54 Q369 35 389 35 Z"
            fill="var(--sky)" filter="url(#tab-shadow)"/>
    </svg>

    <div class="holder">
      <p class="holder-name">DANIEL HART</p>
      <p class="holder-role">Director</p>
    </div>

    <div class="brand">
      <span class="brand-dot"></span>
      <span class="brand-name">
        <span class="main">KESTREL</span>
        <span class="sub">SERVICES</span>
      </span>
    </div>
  </section>
</body>
</html>
```